Need a Wordpress website for my HVAC company

I need a Wordpress website created for an HVAC company in a competitive market.
Following are some websites I like:
My current website is www.borvicoheating.com - we also have a facebook page with some pictures

We are an airconditioning and heating company that does both residential and commmercial work.
We need the following info on our website:
-mobile friendly
-Schedule an appt -repair/maintnenace/installation (i would like this option to always be on the page even if they scroll down.)
-24 hour service
-coupons /promotions
-financing
-reviews/testimonials
-about
-blog
-Our service area
The following are services we provide:
-Air conditioning - Installation/Service/Maintenance/new construction
-Heating - Installation/Service/Maintenance/new construction ( gas furnace, 2 stage furnace, electric heat)
-Duct - Repair/Replacement/Istallation - (zone systems)
-thermostats (wifi)
-Heat pump
-Air handler
-self communicating systems
-carbon monoxide testing
-hail damage
-duct sealing
-insulation
-Air cleaners - UV Air purifiers
-humidifiers

I would also like Quilbo SEO add on

Target Market(s)

Anyone who needs our services HVAC contractor

Industry/Entity Type

Hvac

Contact Information for Business Card

Phone:480-555-2046
website:www.borvicoheating.com
email pmarsh@borvicoheating.com

Coding

Coded - Design and coding required

Number of Pages Required

5+ page

Font styles to use
Serif
Sans Serif

Requirements
Must have
• I wrote in brief. I already have Webly Nest. Long story I paid for 3 years already. I need someone to put website there. Ive never used Wordpress but would like a template page so I can easily add services.
Nice to have
• Clean, bright, original

```html
<!DOCTYPE html>
<html lang="en">
<head>
<meta charset="utf-8">
<title>Borvico Mechanical Services – Heating &amp; Cooling</title>
<link rel="stylesheet" href="https://fonts.googleapis.com/css2?family=PT+Sans:wght@400;700&family=Open+Sans:wght@400;600&display=swap">
<style>
:root{
  --blue:#1b5a97;
  --blue-dark:#134476;
  --ink:#2e2e2e;
  --text:#6b6b6b;
  --muted:#9a9a9a;
  --light:#f5f5f5;
  --line:#e2e2e2;
  --white:#ffffff;
  --red:#c8262c;
}
*{margin:0;padding:0;box-sizing:border-box}
html,body{width:1200px;height:3130px;overflow:hidden}
body{position:relative;background:var(--white);font-family:"Open Sans",Arial,sans-serif;color:var(--text);font-size:12px;line-height:24px}
.abs{position:absolute}
h1,h2,h3,h4{font-family:"PT Sans",Arial,sans-serif;font-weight:400;color:var(--ink)}
.btn{position:absolute;display:flex;align-items:center;justify-content:center;background:var(--blue);color:var(--white);font-family:"PT Sans",Arial,sans-serif;font-weight:700;font-size:11px;letter-spacing:.4px;border-radius:3px;text-transform:uppercase}
.brand{display:flex;align-items:center;gap:12px;font-family:"PT Sans",Arial,sans-serif;font-weight:700;color:var(--blue);text-transform:uppercase}
.brand .dot{border-radius:50%;background:var(--red)}
.ph{position:absolute}

/* header + hero */
.hero{position:absolute;left:0;top:0;width:1200px;height:574px;background:radial-gradient(ellipse at 55% 55%,#ffffff 0%,#f6f6f6 55%,#eeeeee 100%)}
.header-brand{left:135px;top:52px;font-size:30px}
.header-brand .dot{width:34px;height:34px}
.support{left:751px;top:34px;display:flex;align-items:center;font-family:"PT Sans",Arial,sans-serif;font-size:14px}
.support b{color:var(--blue);font-weight:700;margin-right:22px}
.support .ring{width:26px;height:26px;border:1.5px solid var(--ink);border-radius:50%;display:flex;align-items:center;justify-content:center;margin-right:10px}
.support span{color:var(--ink)}
.nav{left:455px;top:88px;font-family:"PT Sans",Arial,sans-serif;font-size:11px;color:var(--ink);text-transform:uppercase}
.nav a{position:absolute;white-space:nowrap;color:var(--ink);text-decoration:none}
.nav a.active{color:var(--blue)}
.hero-kicker{left:131px;top:236px;font-size:29px;letter-spacing:.5px}
.hero-title{left:131px;top:284px;font-size:44px;font-weight:700;letter-spacing:.8px;white-space:nowrap}
.hero-btn{left:131px;top:371px;width:238px;height:50px;font-size:12px}
.dots{position:absolute;display:flex;gap:6px}
.dots i{width:10px;height:10px;border-radius:50%;background:#cfcfcf;display:block}
.dots i.on{background:var(--blue)}
.hero-van{left:548px;top:219px;width:612px;height:236px;border-radius:40px 70px 20px 20px;background:linear-gradient(120deg,#d9dde3 0%,#1d56a8 45%,#2f6fc4 80%,#e9edf2 100%)}

/* welcome */
.welcome-title{left:131px;top:666px;font-size:34px;letter-spacing:.5px}
.welcome-title b{font-weight:700}
.welcome-text{left:131px;top:722px;width:430px;font-size:11px}
.ticks{left:131px;top:784px;list-style:none;font-size:13px;color:var(--ink)}
.ticks li{display:flex;align-items:center;height:29.5px}
.ticks svg{margin-right:18px}
.welcome-btn{left:131px;top:918px;width:96px;height:40px}
.video{left:597px;top:668px;width:469px;height:288px;border:6px solid var(--white);box-shadow:0 0 0 1px var(--line),0 2px 6px rgba(0,0,0,.08);background:linear-gradient(110deg,#d8d6d2 0%,#eeeceb 45%,#c9c6c1 70%,#f1f1f1 100%)}
.play{position:absolute;left:200px;top:104px;width:68px;height:68px;border-radius:50%;border:4px solid rgba(80,80,80,.7);background:rgba(255,255,255,.35)}
.play svg{position:absolute;left:20px;top:15px}

/* residential / commercial */
.residential{left:0;top:1058px;width:1200px;height:459px;background:linear-gradient(90deg,#f2f2f2 0%,#fafafa 45%,#ffffff 100%)}
.res-photo{left:0;top:1058px;width:480px;height:459px;background:linear-gradient(135deg,#e6e6e6 0%,#fbfbfb 45%,#dcdcdc 80%,#efefef 100%)}
.section-title{font-size:33px;letter-spacing:.5px;text-transform:uppercase}
.res-title{left:515px;top:1160px}
.res-text{left:515px;top:1228px;width:540px;font-size:11px}
.res-btn{left:515px;top:1340px;width:97px;height:38px}
.com-title{left:131px;top:1617px}
.com-text{left:131px;top:1685px;width:480px;font-size:11px}
.com-btn{left:131px;top:1786px;width:97px;height:40px}
.com-photo{left:645px;top:1523px;width:440px;height:439px;border-radius:110px 110px 0 0;background:linear-gradient(180deg,#c9b49c 0%,#3f5f88 45%,#e8e8e8 70%,#b9b9b9 100%)}

/* why choose */
.why{left:0;top:1962px;width:1200px;height:455px;background:var(--light)}
.why-title{left:0;top:2024px;width:1200px;text-align:center;font-size:33px}
.feature{position:absolute;width:320px}
.feature svg{position:absolute;left:0;top:0}
.feature h4{position:absolute;left:53px;top:-6px;font-size:18px;white-space:nowrap;text-transform:uppercase}
.feature p{position:absolute;left:53px;top:28px;width:235px;font-size:11px;line-height:24px}

/* testimonials */
.say-title{left:0;top:2464px;width:1200px;text-align:center;font-size:33px}
.quote-mark{left:177px;top:2536px}
.quote{left:267px;top:2542px;width:668px;text-align:center;font-size:11px;line-height:24px}
.author{left:0;top:2641px;width:1200px;text-align:center;color:var(--blue);font-style:italic;font-size:13px}

/* footer */
.footer{left:0;top:2755px;width:1200px;height:375px;background:var(--light)}
.footer-brand{left:136px;top:2830px;font-size:34px}
.footer-brand .dot{width:38px;height:38px}
.f-head{position:absolute;top:2800px;font-size:19px;text-transform:uppercase}
.links{left:440px;top:2841px;list-style:none;font-size:11px;line-height:24px;color:var(--text)}
.contact{left:649px;top:2841px;list-style:none;font-size:11px;color:var(--text)}
.contact li{display:flex;align-items:flex-start;gap:14px;line-height:24px;min-height:28px}
.contact li svg{margin-top:7px;flex:none}
.contact .u{text-decoration:underline}
.social{left:887px;top:2853px;display:flex;gap:7px}
.social i{display:block;width:29px;height:29px;border:1.5px solid var(--ink);border-radius:50%}
.cards{left:887px;top:2955px;display:flex;gap:6px}
.cards i{display:block;width:26px;height:17px;border-radius:2px}
.rule{left:131px;top:3072px;width:938px;height:1px;background:var(--line)}
.copy{left:0;top:3088px;width:1200px;text-align:center;font-size:11px;color:var(--ink)}
</style>
</head>
<body>

<!-- header + hero -->
<section class="hero"></section>
<div class="abs brand header-brand"><span class="dot"></span>Borvico</div>

<div class="abs support">
  <b>24/7 CUSTOMER SUPPORT</b>
  <span class="ring"><svg width="12" height="12" viewBox="0 0 24 24"><path fill="#2e2e2e" d="M6.6 10.8a15 15 0 0 0 6.6 6.6l2.2-2.2c.3-.3.7-.4 1-.2 1.1.4 2.3.6 3.6.6.6 0 1 .4 1 1V20c0 .6-.4 1-1 1A17 17 0 0 1 3 4c0-.6.4-1 1-1h3.5c.6 0 1 .4 1 1 0 1.3.2 2.5.6 3.6.1.3 0 .7-.2 1z"/></svg></span>
  <span>(480) 555-2046</span>
</div>

<nav class="abs nav">
  <a class="active" style="left:0">Home</a>
  <a style="left:69px">About Us</a>
  <a style="left:161px">24 Hour Services</a>
  <a style="left:296px">Coupons</a>
  <a style="left:390px">Reviews</a>
  <a style="left:478px">Blog</a>
  <a style="left:549px">Contact Us</a>
</nav>

<h2 class="abs hero-kicker">REPAIR &amp; MAINTENANCE</h2>
<h1 class="abs hero-title">AIR CONDITIONING</h1>
<a class="btn hero-btn">Schedule an Appointment</a>
<div class="dots" style="left:133px;top:462px"><i class="on"></i><i></i><i></i></div>
<div class="ph hero-van" role="img" aria-label="Branded company service van"></div>

<!-- welcome -->
<h2 class="abs welcome-title">WELCOME TO <b>BORVICO</b></h2>
<p class="abs welcome-text">Borvico Mechanical Services offers many different financing plans. The top reasons to finance with us are:</p>
<ul class="abs ticks">
  <li><svg width="13" height="13" viewBox="0 0 14 14"><circle cx="7" cy="7" r="5.5" fill="none" stroke="#1b5a97" stroke-width="2"/><path d="M5.5 4.5 8 7l-2.5 2.5" fill="none" stroke="#1b5a97" stroke-width="1.6"/></svg>Low cost same as cash financing for qualifying customers.</li>
  <li><svg width="13" height="13" viewBox="0 0 14 14"><circle cx="7" cy="7" r="5.5" fill="none" stroke="#1b5a97" stroke-width="2"/><path d="M5.5 4.5 8 7l-2.5 2.5" fill="none" stroke="#1b5a97" stroke-width="1.6"/></svg>Fast and easy application.</li>
  <li><svg width="13" height="13" viewBox="0 0 14 14"><circle cx="7" cy="7" r="5.5" fill="none" stroke="#1b5a97" stroke-width="2"/><path d="M5.5 4.5 8 7l-2.5 2.5" fill="none" stroke="#1b5a97" stroke-width="1.6"/></svg>Monthly payments as low as $56.90 per month.</li>
  <li><svg width="13" height="13" viewBox="0 0 14 14"><circle cx="7" cy="7" r="5.5" fill="none" stroke="#1b5a97" stroke-width="2"/><path d="M5.5 4.5 8 7l-2.5 2.5" fill="none" stroke="#1b5a97" stroke-width="1.6"/></svg>No lien on your home</li>
</ul>
<a class="btn welcome-btn">Read More</a>
<div class="ph video" role="img" aria-label="Video still of a technician servicing a wall-mounted air conditioner">
  <div class="play"><svg width="26" height="30" viewBox="0 0 26 30"><path d="M2 2l22 13L2 28z" fill="rgba(80,80,80,.75)"/></svg></div>
</div>

<!-- residential -->
<section class="abs residential"></section>
<div class="ph res-photo" role="img" aria-label="Hand pointing a remote at a wall-mounted air conditioning unit"></div>
<h2 class="abs section-title res-title">Residential</h2>
<p class="abs res-text">Borvico Mechanical Services is the premier residential heating, air conditioning, and energy solutions provider in the greater Phoenix area. We can help you lower your energy bills, reduce your environmental impact, and increase the comfort of your home.</p>
<a class="btn res-btn">Read More</a>

<!-- commercial -->
<h2 class="abs section-title com-title">Commercial</h2>
<p class="abs com-text">Borvico Mechanical Services is the premier residential heating, air conditioning, and energy solutions provider in the greater Phoenix area. We can help you lower your energy bills, reduce your environmental impact, and increase the comfort of your home.</p>
<a class="btn com-btn">Read More</a>
<div class="ph com-photo" role="img" aria-label="Technician carrying an air conditioning unit"></div>

<!-- why choose us -->
<section class="abs why"></section>
<h2 class="abs why-title">WHY CHOOSE US</h2>

<div class="feature" style="left:131px;top:2130px">
  <svg width="26" height="26" viewBox="0 0 26 26"><circle cx="13" cy="13" r="10.5" fill="none" stroke="#1b5a97" stroke-width="3"/><path d="M13 7v6.5l4 2.5" fill="none" stroke="#1b5a97" stroke-width="2.4"/></svg>
  <h4>24/7 Emergency Service</h4>
  <p>You need air conditioning service when you need it, not when we feel like being open.</p>
</div>
<div class="feature" style="left:459px;top:2130px">
  <svg width="28" height="26" viewBox="0 0 28 26"><rect x="2" y="4" width="24" height="20" fill="none" stroke="#1b5a97" stroke-width="2.4"/><rect x="2" y="4" width="24" height="5" fill="#1b5a97"/><path d="M7 1v5M21 1v5" stroke="#1b5a97" stroke-width="2.4"/><path d="M6 13h4M12 13h4M18 13h4M6 18h4M12 18h4M18 18h4" stroke="#1b5a97" stroke-width="2.4"/></svg>
  <h4>Same Day Service</h4>
  <p>You need air conditioning service when you need it, not when we feel like being open.</p>
</div>
<div class="feature" style="left:787px;top:2130px">
  <svg width="28" height="28" viewBox="0 0 28 28"><path d="M4 25l11-11" stroke="#1b5a97" stroke-width="4" stroke-linecap="round"/><circle cx="19" cy="9" r="6.5" fill="#1b5a97"/><path d="M19 2l5 5-3 1-3-3z" fill="#f5f5f5"/></svg>
  <h4>Trained Technicians</h4>
  <p>You need air conditioning service when you need it, not when we feel like being open.</p>
</div>
<div class="feature" style="left:131px;top:2259px">
  <svg width="26" height="28" viewBox="0 0 26 28"><path d="M15 1L6 16h6l-3 11 10-16h-6l3-10z" fill="#1b5a97"/></svg>
  <h4>Free Energy Survey</h4>
  <p>You need air conditioning service when you need it, not when we feel like being open.</p>
</div>
<div class="feature" style="left:459px;top:2259px">
  <svg width="28" height="24" viewBox="0 0 28 24"><rect x="2" y="3" width="24" height="18" rx="2" fill="none" stroke="#1b5a97" stroke-width="2.4"/><rect x="2" y="8" width="24" height="4" fill="#1b5a97"/><path d="M6 16h7" stroke="#1b5a97" stroke-width="2.4"/></svg>
  <h4>Pay by the Job</h4>
  <p>You need air conditioning service when you need it, not when we feel like being open.</p>
</div>
<div class="feature" style="left:787px;top:2259px">
  <svg width="30" height="28" viewBox="0 0 30 28"><path d="M15 1L2 8h26z" fill="#1b5a97"/><rect x="3" y="9" width="24" height="2.5" fill="#1b5a97"/><path d="M6 13v9M12 13v9M18 13v9M24 13v9" stroke="#1b5a97" stroke-width="3"/><rect x="2" y="23" width="26" height="3" fill="#1b5a97"/></svg>
  <h4>Fairness and Honesty</h4>
  <p>You need air conditioning service when you need it, not when we feel like being open.</p>
</div>

<!-- testimonials -->
<h2 class="abs say-title">OUR CUSTOMERS SAY...</h2>
<svg class="abs quote-mark" width="54" height="32" viewBox="0 0 54 32"><path d="M12 0h14L14 32H0zM38 0h14L40 32H26z" fill="#c9c9c9"/></svg>
<p class="abs quote">Nemo enim ipsam voluptatem quia voluptas sit aspernatur aut odit aut fugit, sed quia consequuntur magni dolores eos qui ratione voluptatem sequi nesciunt. Neque porro quisquam est, qui dolorem ipsum quia dolor sit amet, consectetur, adipisci velit, sed quia non numquam eius modi tempora incidunt ut labore et dolore magnam aliquam quaerat voluptatem.</p>
<p class="abs author">- Dana Ortiz -</p>
<div class="dots" style="left:579px;top:2700px"><i class="on"></i><i></i><i></i></div>

<!-- footer -->
<footer class="abs footer"></footer>
<div class="abs brand footer-brand"><span class="dot"></span>Borvico</div>

<h3 class="f-head" style="left:440px">Quick Links</h3>
<ul class="abs links">
  <li>Home</li><li>About us</li><li>24 hour services</li><li>Coupons</li><li>Financing</li><li>Reviews</li><li>Blog</li><li>Contact us</li>
</ul>

<h3 class="f-head" style="left:649px">Contact Us</h3>
<ul class="abs contact">
  <li><svg width="12" height="11" viewBox="0 0 12 11"><path d="M1 3c2-2 8-2 10 0v2H8V4H4v1H1zM2 6h8l1 4H1z" fill="#555"/></svg>201-555-0178</li>
  <li><svg width="12" height="11" viewBox="0 0 12 11"><rect x="3" y="0" width="6" height="3" fill="#555"/><rect x="0" y="3" width="12" height="5" fill="#555"/><rect x="3" y="7" width="6" height="4" fill="#555"/></svg>201-555-0178</li>
  <li><svg width="12" height="9" viewBox="0 0 12 9"><rect x=".5" y=".5" width="11" height="8" fill="none" stroke="#555"/><path d="M.5.5 6 5 11.5.5" fill="none" stroke="#555"/></svg><span class="u">info@borvicoheating.com</span></li>
  <li><svg width="10" height="13" viewBox="0 0 10 13"><path d="M5 0a5 5 0 0 1 5 5c0 3-5 8-5 8S0 8 0 5a5 5 0 0 1 5-5z" fill="#555"/><circle cx="5" cy="5" r="1.8" fill="#f5f5f5"/></svg><span style="line-height:16px;padding-top:4px">#2868 Lorem ipsum dolor sit<br>amet, consectetur</span></li>
</ul>

<h3 class="f-head" style="left:887px">Follow Us</h3>
<div class="abs social" aria-label="Social links"><i></i><i></i><i></i><i></i><i></i></div>

<h3 class="f-head" style="left:887px;top:2910px">We Accept</h3>
<div class="abs cards" aria-label="Accepted payment cards">
  <i style="background:#e8912c"></i><i style="background:#2b58a8"></i><i style="background:#d6452e"></i><i style="background:#3f8fd2"></i>
</div>

<div class="abs rule"></div>
<p class="abs copy">© 2016 Borvicoheating.com. All rights reserved.</p>

</body>
</html>
```